Business card design for a dynamic IT consulting company

We need a business card design for a young firm, specialized in the Telecommunications/Consulting industry. The name of the company is Quindor and Partners Business Consulting Ltd. (Short name: Quindor and Partnes)
Quindor = solve read reverse, so we aim to be uncomplicated and solution-oriented. The small pipe in our logo is also related to the word solve. So we need a new business card design, which is simple, eye catching and something non traditional (I would probably prefer a square shaped design rather than a rectangle, but open for suggestions). Attached our logo.

Target Market(s)

Usually our customers are Tier1 Telecoms providers (Q-Netra, Palorix, etc) and their executives.

Industry/Entity Type

Business

Contact Information for Business Card

Name: Bence Tolnavari
Email: b.tolnavari@quindor.hu
Web: www.quindor.hu
Mobile: +36 30 518 2769
Title: Managing Director

Optional:
Company name: Quindor and Partners Ltd.
Address: 1087 Budapest, Tolvenka str. 28/C, Hungary

Font styles to use
Other font styles liked:
• helveticaneue_medium, Prime Regular are used now.

Colors

Designer to choose colors to be used in the design.

Requirements
Must have
• I would like to have a 2 sided design.
Nice to have
• I thought if we make the logo a bit bigger (without the company name), that could go to the back with the company name below. I though, if the pipe in the logo is somehow touchable on the business card, would be nice and unique.

```html
<!DOCTYPE html>
<html lang="en">
<head>
<meta charset="utf-8">
<title>Quindor – Business Card</title>
<link rel="stylesheet" href="https://fonts.googleapis.com/css2?family=Work+Sans:wght@300;400;600&display=swap">
<style>
  :root {
    --stage: #1c1d20;
    --card-white: #ffffff;
    --card-fog: #eef0f2;
    --brand-blue: #1e96d6;
    --brand-blue-deep: #157fbd;
    --brand-magenta: #a8338f;
    --ink: #4a4a4c;
    --ink-soft: #6b6b6e;
    --rule: #7a7a7c;
    --paper-light: #f4f8fb;
  }
  * { box-sizing: border-box; margin: 0; padding: 0; }
  html, body { width: 1200px; height: 963px; overflow: hidden; }
  body {
    background: var(--stage);
    font-family: "Work Sans", Arial, sans-serif;
    display: flex;
    flex-direction: column;
    align-items: center;
    justify-content: center;
    gap: 60px;
  }
  .card {
    position: relative;
    width: 680px;
    height: 400px;
    border-radius: 22px;
    overflow: hidden;
  }

  /* Front */
  .card-front {
    background: linear-gradient(160deg, var(--card-fog) 0%, var(--card-white) 45%);
  }
  .front-wave { position: absolute; inset: 0; width: 100%; height: 100%; }
  .brand-mark {
    position: absolute;
    left: 70px;
    top: 120px;
    display: flex;
    align-items: center;
    gap: 14px;
  }
  .brand-mark-square {
    width: 26px; height: 26px;
    background: var(--brand-magenta);
  }
  .brand-mark-name {
    font-size: 40px;
    font-weight: 400;
    color: var(--ink);
    letter-spacing: 0.5px;
  }
  .divider {
    position: absolute;
    left: 320px;
    top: 110px;
    width: 1.5px;
    height: 170px;
    background: var(--rule);
  }
  .contact {
    position: absolute;
    left: 346px;
    top: 110px;
    color: var(--ink-soft);
    font-size: 15px;
    line-height: 1.35;
  }
  .contact-name {
    font-size: 25px;
    font-weight: 600;
    color: var(--brand-blue);
    line-height: 1.1;
  }
  .contact-title { font-size: 16px; margin-bottom: 6px; }
  .contact-address { margin-bottom: 10px; }
  .contact-line { display: flex; align-items: center; gap: 8px; }
  .contact-icon { width: 13px; height: 13px; flex: none; }

  /* Back */
  .card-back {
    background: radial-gradient(ellipse at 40% 40%, #2aa3de 0%, var(--brand-blue) 45%, var(--brand-blue-deep) 100%);
    display: flex;
    align-items: center;
    justify-content: center;
  }
  .back-lockup {
    display: flex;
    align-items: center;
    gap: 22px;
  }
  .back-square { width: 34px; height: 34px; background: var(--paper-light); }
  .back-name {
    font-size: 64px;
    font-weight: 300;
    line-height: 1;
    color: var(--paper-light);
  }
</style>
</head>
<body>

  <section class="card card-front" aria-label="Business card front">
    <svg class="front-wave" viewBox="0 0 680 400" preserveAspectRatio="none" aria-hidden="true">
      <path d="M0 255 C 120 330, 300 330, 420 350 C 470 360, 500 380, 510 400 L 0 400 Z" fill="var(--brand-blue)"/>
      <path d="M0 244 C 120 322, 300 322, 420 341 C 475 352, 505 374, 518 400" fill="none" stroke="var(--brand-magenta)" stroke-width="4"/>
    </svg>

    <div class="brand-mark">
      <span class="brand-mark-square"></span>
      <span class="brand-mark-name">Quindor</span>
    </div>

    <div class="divider"></div>

    <div class="contact">
      <p class="contact-name">Bence Tolnavari</p>
      <p class="contact-title">Managing Director</p>
      <p class="contact-address">1087 Budapest,<br>Tolvenka str. 28/C, Hungary</p>
      <p class="contact-line">
        <svg class="contact-icon" viewBox="0 0 16 16" aria-hidden="true"><path d="M3 1h3l1.5 4-2 1.2a9 9 0 0 0 4.3 4.3L11 8.5l4 1.5v3c0 1-1 2-2 2C6.5 15 1 9.5 1 3c0-1 1-2 2-2z" fill="var(--brand-blue)"/></svg>
        +36 30 518 2769
      </p>
      <p class="contact-line">
        <svg class="contact-icon" viewBox="0 0 16 16" aria-hidden="true"><rect x="1" y="3" width="14" height="10" fill="none" stroke="var(--brand-blue)" stroke-width="1.6"/><path d="M1 3l7 6 7-6" fill="none" stroke="var(--brand-blue)" stroke-width="1.6"/></svg>
        b.tolnavari@quindor.hu
      </p>
      <p class="contact-line">
        <svg class="contact-icon" viewBox="0 0 16 16" aria-hidden="true"><circle cx="8" cy="8" r="6.5" fill="none" stroke="var(--brand-blue)" stroke-width="1.5"/><ellipse cx="8" cy="8" rx="2.8" ry="6.5" fill="none" stroke="var(--brand-blue)" stroke-width="1.2"/><path d="M1.5 8h13" stroke="var(--brand-blue)" stroke-width="1.2"/></svg>
        www.quindor.hu
      </p>
    </div>
  </section>

  <section class="card card-back" aria-label="Business card back">
    <div class="back-lockup">
      <span class="back-square"></span>
      <p class="back-name">Quindor</p>
    </div>
  </section>

</body>
</html>
```